Blind Rivet Product catalogue

Need a design in wordpress with a productcatalogue where i present all products. This is a B2B business. The products is Blindrivets and Blindrivet nuts and accessories to this. I only want the basic information and also technical specification.

This is a subcompany to my existing company k7.m3.se but specializing in a subcategory

Businesses using blind rivet technology.

Industrial

Sans Serif

Must have
• Three different categories for the products; Blind Rivets - Blind Rivet Nut - Riveting Tools
Nice to have
• Possible to ad login for more information of the different sizes

```html
<!DOCTYPE html>
<html lang="en">
<head>
<meta charset="utf-8">
<title>K7M3 Stainless Solutions</title>
<link href="https://fonts.googleapis.com/css2?family=Audiowide&family=Roboto:wght@300;400;500;700&display=swap" rel="stylesheet">
<style>
:root{
  --green:#6ab04c;
  --red:#e02020;
  --black:#0b0b0b;
  --dark:#151515;
  --text:#555;
  --white:#fff;
}
*{margin:0;padding:0;box-sizing:border-box}
html,body{width:1200px;height:2986px;overflow:hidden}
body{font-family:'Roboto',sans-serif;background:var(--white);position:relative;color:#222}
.abs{position:absolute}
.display{font-family:'Audiowide',sans-serif}

/* header */
.site-header{left:0;top:0;width:1200px;height:101px;background:var(--black)}
.brand{left:90px;top:30px;display:flex;align-items:center;gap:8px;color:var(--white);font-size:24px;font-weight:700;letter-spacing:1px}
.brand-mark{width:18px;height:18px;background:var(--green)}
.search{left:357px;top:12px;width:289px;height:40px;background:#1d1d1d;border-radius:3px;color:#ddd;font-size:16px;display:flex;align-items:center;gap:10px;padding-left:16px}
.utility{top:22px;color:#eee;font-size:16px;display:flex;align-items:center;gap:8px}
.main-nav{top:64px;right:90px;display:flex;gap:30px;font-size:15.5px;color:#eee}
.main-nav .active{color:var(--green)}

/* hero */
.hero{left:0;top:101px;width:1200px;height:546px;background:linear-gradient(120deg,#4a5368 0%,#2b3447 40%,#6a7288 70%,#3a4256 100%)}
.hero-title{left:0;width:1200px;text-align:center;color:var(--white)}
.hero-l1{top:222px;font-size:70px}
.hero-l2{top:290px;font-size:70px}
.hero-l2 small{font-size:48px}
.hero-text{left:180px;top:372px;width:840px;text-align:center;color:var(--white);font-size:23px;font-weight:500;line-height:29px}
.btn{background:var(--green);color:var(--white);border-radius:30px;display:flex;align-items:center;justify-content:center;font-weight:500}
.hero-btn{left:507px;top:459px;width:188px;height:53px;font-size:20px}

/* about */
.about-frame{left:111px;top:756px;width:426px;height:456px;background:var(--green)}
.about-photo{left:121px;top:747px;width:425px;height:456px;background:linear-gradient(135deg,#6f6a5e,#a59a8a 45%,#d8d4cf 70%,#7a7670)}
.section-title{font-size:44px;color:#111}
.divider{display:flex;gap:10px}
.divider i{display:block;width:18px;height:3px;background:var(--green)}
.divider i+i{background:var(--red)}
.about-title{left:600px;top:792px}
.about-div{left:600px;top:855px}
.about-text{left:600px;top:885px;width:500px;font-size:15.6px;line-height:30.4px;color:var(--text);font-weight:300}
.about-btn{left:600px;top:1097px;width:152px;height:50px;font-size:16px}

/* featured */
.featured{left:0;top:1312px;width:1200px;height:627px;background:linear-gradient(90deg,#65a846,#6fb14f 60%,#5e9e40)}
.featured-title{left:0;width:1200px;top:1402px;text-align:center;color:var(--white);font-size:42px}
.featured-div{left:578px;top:1464px}
.featured-div i:first-child{background:var(--white)}
.product{width:304px;height:304px;border-radius:50%;background:var(--white);top:1498px;display:flex;align-items:center;justify-content:center}
.product-art{width:150px;height:90px;border-radius:45px;background:linear-gradient(90deg,#bfbfbf,#eee,#999)}
.product-label{top:1812px;width:304px;text-align:center;color:var(--white);font-size:23px;font-weight:500}

/* news */
.news-title{left:0;width:1200px;text-align:center;top:2028px}
.news-div{left:578px;top:2093px}
.card{border:1px solid #ddd;background:var(--white);overflow:hidden}
.card-img{background:linear-gradient(135deg,#333,#6b7a8a 50%,#c9c3bd)}
.card h3{font-size:18px;font-weight:500;color:#222;line-height:30px}
.meta{font-size:13px;color:#666;display:flex;align-items:center;gap:6px}
.card p{font-size:15px;color:#555;line-height:24px}
.card .lead-text{font-size:14.5px;line-height:25px;margin:8px 14px 0 18px}

/* footer */
.site-footer{left:0;top:2624px;width:1200px;height:362px;background:var(--dark);color:#eee}
.foot-h{font-size:22px;font-weight:700;color:var(--white)}
.foot-small{font-size:13px;line-height:18px;color:#ddd}
.foot-links{font-size:13px;line-height:27px;color:#ddd}
.vline{width:1px;height:186px;background:#333;top:2712px}
.news-input{left:832px;top:2806px;width:283px;height:40px;background:var(--white);font-size:11px;color:#888;display:flex;align-items:center;padding-left:14px}
.news-send{left:1073px;top:2806px;width:42px;height:40px;background:var(--green);display:flex;align-items:center;justify-content:center}
.social{top:2874px;width:34px;height:34px;border-radius:50%;background:var(--green)}
.copy{left:0;width:1200px;top:2956px;text-align:center;font-size:11px;color:#ddd}
</style>
</head>
<body>

<header class="abs site-header">
  <div class="abs brand"><span class="brand-mark"></span>K7M3</div>
  <div class="abs search">
    <svg width="16" height="16" viewBox="0 0 16 16"><circle cx="6.5" cy="6.5" r="4.8" fill="none" stroke="#fff" stroke-width="2"/><line x1="10" y1="10" x2="14.5" y2="14.5" stroke="#fff" stroke-width="2.4"/></svg>
    Search
  </div>
  <div class="abs utility" style="left:683px">
    <svg width="16" height="14" viewBox="0 0 16 14"><path d="M0 1h3l2 8h9l2-6H5" fill="none" stroke="#fff" stroke-width="1.6"/><circle cx="6" cy="12" r="1.4" fill="#fff"/><circle cx="13" cy="12" r="1.4" fill="#fff"/></svg>
    The Cart Is Empty
  </div>
  <div class="abs utility" style="left:855px">|</div>
  <div class="abs utility" style="left:887px">
    <svg width="12" height="14" viewBox="0 0 12 14"><rect x="1" y="6" width="10" height="8" fill="#fff"/><path d="M3 6V4a3 3 0 0 1 6 0v2" fill="none" stroke="#fff" stroke-width="1.6"/></svg>
    Inloggning
  </div>
  <div class="abs utility" style="left:1004px">|</div>
  <div class="abs utility" style="left:1033px">
    <svg width="14" height="14" viewBox="0 0 14 14"><path d="M1 13l1-4 8-8 3 3-8 8z" fill="#fff"/></svg>
    Register
  </div>
  <nav class="abs main-nav">
    <span class="active">Marin</span><span>Screw</span><span>Sticks</span><span>Nuts</span><span>Trays</span><span>Screw Pin</span><span>Other Attachment</span><span>Contact Us</span><span>About Us</span><span>Sitemap</span>
  </nav>
</header>

<section class="abs hero" role="img" aria-label="Close-up of an industrial riveting machine working on metal"></section>
<h1 class="abs hero-title hero-l1 display">WELCOME TO</h1>
<div class="abs hero-title hero-l2 display">K7M3 <small>STAINLESS SOLUTIONS</small></div>
<p class="abs hero-text">Lorem ipsum dolor sit amet, consectetur adipiscing elit, sed do eiusmod tempor incididunt ut labore et dolore magna aliqua.</p>
<div class="abs btn hero-btn">Get Started</div>

<div class="abs about-frame"></div>
<div class="abs about-photo" role="img" aria-label="Hand using riveting pliers on a stainless steel tube"></div>
<h2 class="abs section-title display about-title">About Us</h2>
<div class="abs divider about-div"><i></i><i></i></div>
<p class="abs about-text">Lorem ipsum dolor sit amet, consectetur adipiscing elit, sed do mod tempor incididunt ut labore et dolore magna aliqua. Ut enim ad minim veniam, quis nostrud exercitation ullamco laboris nisi ut aliquip ex ea commodo consequat. Duis aute irure dolor in reprehenderit in luptate velit esse cillum dolore eu fugiat nulla pariatur. Excepteur sint tat non proident, sunt in culpa qui officia mollit anim id laborum</p>
<div class="abs btn about-btn">Read More</div>

<section class="abs featured"></section>
<h2 class="abs featured-title display">Featured Products</h2>
<div class="abs divider featured-div"><i></i><i></i></div>
<div class="abs product" style="left:109px"><div class="product-art" role="img" aria-label="Blind rivet"></div></div>
<div class="abs product" style="left:449px"><div class="product-art" style="width:110px;height:110px;border-radius:20px" role="img" aria-label="Blind rivet nut"></div></div>
<div class="abs product" style="left:788px"><div class="product-art" style="width:90px;height:130px;border-radius:12px;background:linear-gradient(#222,#444)" role="img" aria-label="Cordless riveting tool"></div></div>
<div class="abs product-label" style="left:109px">Blind Rivets</div>
<div class="abs product-label" style="left:449px">Blind Rivet Nut</div>
<div class="abs product-label" style="left:788px">Riveting Tools</div>

<h2 class="abs section-title display news-title">Latest News</h2>
<div class="abs divider news-div"><i></i><i></i></div>

<article class="abs card" style="left:89px;top:2120px;width:514px;height:403px">
  <div class="card-img" style="height:259px" role="img" aria-label="Worker operating a bench press riveting machine"></div>
  <h3 style="margin:18px 0 0 18px">Lorem ipsum dolor sit amet, consectetur adipiscing</h3>
  <div class="meta" style="margin:2px 0 0 18px"><svg width="11" height="11" viewBox="0 0 11 11"><rect x="0.5" y="1.5" width="10" height="9" fill="none" stroke="#666"/><rect x="0.5" y="1.5" width="10" height="2.5" fill="#666"/></svg>7/19/19</div>
  <p class="lead-text">Lorem ipsum dolor sit amet, consectetur adipiscing elit, sed do eiusmod tempor incididunt ut labore et dolore magna aliqua. Ut enim ad minim</p>
</article>

<article class="abs card" style="left:612px;top:2120px;width:498px;height:196px">
  <div class="abs card-img" style="left:0;top:0;width:250px;height:194px" role="img" aria-label="Riveting tool fastening a metal tube"></div>
  <div class="abs" style="left:268px;top:14px;width:214px">
    <h3>Lorem ipsum dolor sit</h3>
    <div class="meta" style="margin-top:4px"><svg width="11" height="11" viewBox="0 0 11 11"><rect x="0.5" y="1.5" width="10" height="9" fill="none" stroke="#666"/><rect x="0.5" y="1.5" width="10" height="2.5" fill="#666"/></svg>7/19/19</div>
    <p style="margin-top:12px;font-size:14.5px">Lorem ipsum dolor sit amet, usmod tempor incididunt ut labore et d veniam,...<span style="font-size:12px;color:#333">Read More</span></p>
  </div>
</article>

<article class="abs card" style="left:612px;top:2328px;width:498px;height:195px">
  <div class="abs" style="left:22px;top:18px;width:200px">
    <h3>Lorem ipsum dolor sit amet, consectetur adipiscing</h3>
    <div class="meta" style="margin-top:12px"><svg width="11" height="11" viewBox="0 0 11 11"><rect x="0.5" y="1.5" width="10" height="9" fill="none" stroke="#666"/><rect x="0.5" y="1.5" width="10" height="2.5" fill="#666"/></svg>7/19/19</div>
  </div>
  <div class="abs card-img" style="left:248px;top:0;width:249px;height:193px;background:linear-gradient(135deg,#c9985c,#e0b67a 50%,#a87a48)" role="img" aria-label="Yellow hand riveter with loose rivets on wood"></div>
</article>

<footer class="abs site-footer"></footer>
<div class="abs foot-h" style="left:89px;top:2696px">Contact Us</div>
<div class="abs foot-small" style="left:89px;top:2744px">Company<br>14 Harbour Road, Westbay 4500</div>
<div class="abs foot-small" style="left:86px;top:2803px">Email address<br>info@k7m3-mail.se</div>
<div class="abs foot-small" style="left:88px;top:2862px">Call us<br>0300-41 62 08</div>
<div class="abs vline" style="left:370px"></div>
<div class="abs foot-h" style="left:422px;top:2696px">Links</div>
<div class="abs foot-links" style="left:424px;top:2736px">Marin<br>Screw<br>Sticks<br>Nuts<br>Trays</div>
<div class="abs vline" style="left:580px"></div>
<div class="abs foot-links" style="left:625px;top:2736px">Screw Pin<br>Other Attachment<br>Contact Us<br>About Us<br>Sitemap</div>
<div class="abs vline" style="left:767px"></div>
<div class="abs foot-h" style="left:829px;top:2696px">Newsletter</div>
<div class="abs foot-small" style="left:830px;top:2746px;width:270px;line-height:22px">For exclusive news and updates sign up for our newsletter.</div>
<div class="abs news-input">Email Address</div>
<div class="abs news-send"><svg width="18" height="18" viewBox="0 0 18 18"><path d="M1 9L17 1 12 17 9 10z" fill="none" stroke="#fff" stroke-width="1.6"/></svg></div>
<div class="abs social" style="left:831px"></div>
<div class="abs social" style="left:878px"></div>
<div class="abs social" style="left:925px"></div>
<div class="abs social" style="left:972px"></div>
<div class="abs social" style="left:1019px"></div>
<div class="abs copy">© 2020 Copyrights.THE COMPANY NAME.All Rights Reserved | Privacy Policy, Terms of Service</div>

</body>
</html>
```